Wine Label for a Sweet Wine Called "Glimmo"

We need a wine label that will be used for both a sweet red and a sweet white wine. The very important thing to remember is the target market for these wines is: young American women who love sweet wines and they also spend a lot of their money on their hair, clothes, jewelry, nails. They LOVE Glimmo (Glimmo is a word used to describe flashy accessories, jewelry, decoration.) This label needs to be eye catching, showy, fun, glittery. Please put the brand name, "Glimmo," big, and then in smaller but still readable words underneath the label or somewhere on the label: Sweet, Sophisticated, Red (or white). (An example of what I mean is attached). To differentiate between the two color wines you can suggest color changes to differentiate between the red label and the white label but the label design itself should be the same. Ultimately, the label can be the exact same label for both white and red as long as it looks good on a white wine (a greenish/yellow wine in a clear glass bottle) and a red wine (a dark color wine in a dark bottle).

I've attached an example of the text size relationship between the word Glimmo and the words to go underneath or elsewhere on the label, but you can certainly play with this-- it is just a suggestion of the text size relationship, and definitely NOT at all mandatory that you use any of these fonts.

You can pick the size of the label but try to stay within normal wine label sizes, meaning don't go bigger than approx. 3.5 inches wide and 5 inches tall.

Target Market(s)

Young American women who love sweet wines and spend a lot of money on their hair, clothes, jewelry, nails. They love Glimmo (Glimmo is a word that means flashy accessories, jewelry, decoration)

Requirements
Must have
• It needs to be flashy, glittery, fun, eye catching, memorable
Nice to have
• It shouldn't be too too ultra feminine! The target market is strong independent women and we also have men who will buy it too.

```html
<!DOCTYPE html>
<html lang="en">
<head>
<meta charset="utf-8">
<title>Glimmo Wine Labels</title>
<link href="https://fonts.googleapis.com/css2?family=Pinyon+Script&family=Montserrat:wght@500&display=swap" rel="stylesheet">
<style>
  :root {
    --page-bg: #ffffff;
    --gold-light: #fff6c4;
    --gold-mid: #f0c95a;
    --gold-deep: #d9a21c;
    --white-center: #d9b728;
    --white-edge: #66792a;
    --white-ornament: #55672a;
    --white-title: #dbeaf4;
    --red-center: #c35a2e;
    --red-edge: #5a150f;
    --red-ornament: #3e0d0a;
    --red-title: #ffffff;
    --diamond-light: #eef6fb;
    --diamond-mid: #a9cbe4;
    --tagline: #f3f0e2;
  }
  * { box-sizing: border-box; margin: 0; padding: 0; }
  html, body {
    width: 1011px;
    height: 1200px;
    overflow: hidden;
    background: var(--page-bg);
  }
  .canvas {
    position: relative;
    width: 1011px;
    height: 1200px;
  }
  .label {
    position: absolute;
    left: 355px;
    width: 300px;
    height: 428px;
    padding: 10px;
    background: linear-gradient(135deg, var(--gold-deep) 0%, var(--gold-light) 30%, var(--gold-mid) 60%, var(--gold-light) 85%, var(--gold-deep) 100%);
  }
  .label--white { top: 75px; }
  .label--red { top: 668px; }
  .label__panel {
    position: relative;
    width: 100%;
    height: 100%;
    overflow: hidden;
  }
  .label--white .label__panel {
    background: radial-gradient(ellipse at 50% 42%, var(--white-center) 0%, #a6a226 45%, var(--white-edge) 100%);
  }
  .label--red .label__panel {
    background: radial-gradient(ellipse at 50% 42%, var(--red-center) 0%, #8e2e1a 45%, var(--red-edge) 100%);
  }
  .ornament {
    position: absolute;
    opacity: 0.55;
  }
  .ornament--left, .ornament--right { top: 8px; bottom: 8px; width: 34px; }
  .ornament--left { left: 4px; }
  .ornament--right { right: 4px; }
  .ornament--top, .ornament--bottom { left: 40px; right: 40px; height: 24px; }
  .ornament--top { top: 4px; }
  .ornament--bottom { bottom: 4px; }
  .label--white .ornament--left,
  .label--white .ornament--right { background: linear-gradient(90deg, transparent, var(--white-ornament), transparent); }
  .label--white .ornament--top,
  .label--white .ornament--bottom { background: linear-gradient(180deg, transparent, var(--white-ornament), transparent); }
  .label--red .ornament--left,
  .label--red .ornament--right { background: linear-gradient(90deg, transparent, var(--red-ornament), transparent); }
  .label--red .ornament--top,
  .label--red .ornament--bottom { background: linear-gradient(180deg, transparent, var(--red-ornament), transparent); }
  .brand-name {
    position: absolute;
    top: 72px;
    left: 0;
    right: 0;
    text-align: center;
    font-family: "Pinyon Script", cursive;
    font-size: 66px;
    font-weight: 400;
    line-height: 1;
  }
  .label--white .brand-name { color: var(--white-title); }
  .label--red .brand-name { color: var(--red-title); }
  .gem-art {
    position: absolute;
    top: 178px;
    left: 62px;
    width: 156px;
    height: 94px;
    background: linear-gradient(180deg, var(--diamond-light) 0%, var(--diamond-mid) 100%);
    opacity: 0.9;
  }
  .divider {
    position: absolute;
    top: 340px;
    left: 40px;
    right: 40px;
    height: 1px;
  }
  .label--white .divider { background: #8f9a4a; }
  .label--red .divider { background: #6f7a33; }
  .tagline {
    position: absolute;
    top: 351px;
    left: 0;
    right: 0;
    text-align: center;
    font-family: "Montserrat", sans-serif;
    font-weight: 500;
    font-size: 8.5px;
    letter-spacing: 0.9px;
    color: var(--tagline);
  }
</style>
</head>
<body>
<main class="canvas">

  <section class="label label--white">
    <div class="label__panel">
      <div class="ornament ornament--left" role="img" aria-label="Decorative vine scrollwork border"></div>
      <div class="ornament ornament--right" role="img" aria-label="Decorative vine scrollwork border"></div>
      <div class="ornament ornament--top" role="img" aria-label="Decorative scrollwork trim"></div>
      <div class="ornament ornament--bottom" role="img" aria-label="Decorative scrollwork trim"></div>
      <h1 class="brand-name">Glimmo</h1>
      <div class="gem-art" role="img" aria-label="Illustration of a sparkling cut diamond"></div>
      <div class="divider"></div>
      <p class="tagline">SWEET | SOPHISTICATED | RED</p>
    </div>
  </section>

  <section class="label label--red">
    <div class="label__panel">
      <div class="ornament ornament--left" role="img" aria-label="Decorative vine scrollwork border"></div>
      <div class="ornament ornament--right" role="img" aria-label="Decorative vine scrollwork border"></div>
      <div class="ornament ornament--top" role="img" aria-label="Decorative scrollwork trim"></div>
      <div class="ornament ornament--bottom" role="img" aria-label="Decorative scrollwork trim"></div>
      <h2 class="brand-name">Glimmo</h2>
      <div class="gem-art" role="img" aria-label="Illustration of a sparkling cut diamond"></div>
      <div class="divider"></div>
      <p class="tagline">SWEET | SOPHISTICATED | RED</p>
    </div>
  </section>

</main>
</body>
</html>
```